Business Card Re-Design/Update

We'd like to update out business cards. I've included our current "Style guide" which has the colour scheme of the organisation in it. I've also included the branding files with logos etc in them.

I've also included a copy of one of our existing cards so that you can see how ugly/dated they look. I'd like a fresh modern corporate look.

Target Market(s)

These are for our clients, potential clients, industry contacts - like all business cards

Contact Information for Business Card

Name
Position
Company Address - Level 1, 47 Fernby Street, Carlow Qld 4072
Direct Phone
mobile
Email
Website -www.korvalit.com.au
Logo

Colors

Designer to choose colors to be used in the design.

Requirements
Must have
• Main Logo
• Cards will need to be editable to be able to personalize them for each new employee.
Nice to have
• The MapOut, ShipWell, KeepSteady would be okay to have if they can be sensibly and professionally added to the look without detracting from the main imagery.
• Maybe they could go on the back of the card? will leave this to your creative discretion as to whether/where they fit.
Should not have
• Should not have decorative or script fonts

```html
<!DOCTYPE html>
<html lang="en">
<head>
<meta charset="utf-8">
<title>KorvalIT Business Card</title>
<link rel="stylesheet" href="https://fonts.googleapis.com/css2?family=Work+Sans:wght@400;500&display=swap">
<style>
  :root {
    --brand-blue: #1f86c9;
    --rule-blue: #6fb3e0;
    --ink: #2b2b2b;
    --ink-soft: #4a4a4a;
    --card-white: #ffffff;
    --card-dark: #2a2b2d;
    --backdrop: #d8dbde;
  }
  * { margin: 0; padding: 0; box-sizing: border-box; }
  html, body { width: 1200px; height: 900px; overflow: hidden; }
  body {
    background: var(--backdrop);
    font-family: "Work Sans", Arial, sans-serif;
    position: relative;
  }
  .card {
    position: absolute;
    left: 250px;
    width: 700px;
    height: 400px;
    border-radius: 4px;
    overflow: hidden;
    box-shadow: 0 8px 24px rgba(0,0,0,0.18);
  }
  .card-front { top: 40px; background: linear-gradient(135deg, #f1f2f3 0%, var(--card-white) 55%); }
  .card-back { top: 460px; background: var(--card-dark); }

  .brand {
    position: absolute;
    display: flex;
    align-items: center;
    gap: 14px;
    color: var(--brand-blue);
    font-weight: 500;
  }
  .brand-square { background: var(--brand-blue); }
  .card-front .brand { left: 50px; top: 42px; font-size: 42px; letter-spacing: -0.5px; }
  .card-front .brand-square { width: 30px; height: 30px; }

  .person {
    position: absolute;
    right: 70px;
    top: 108px;
    text-align: right;
  }
  .person-name { color: var(--brand-blue); font-size: 27px; font-weight: 500; letter-spacing: 0.5px; }
  .person-role { color: var(--ink-soft); font-size: 16px; margin-top: 2px; }

  .divider {
    position: absolute;
    left: 50px;
    right: 70px;
    top: 178px;
    height: 1.5px;
    background: var(--rule-blue);
  }

  .contacts {
    position: absolute;
    left: 50px;
    top: 196px;
    list-style: none;
    font-size: 16px;
    color: var(--ink);
    line-height: 24px;
  }
  .contacts li { display: flex; align-items: center; gap: 10px; }
  .contacts svg { width: 13px; height: 13px; flex: none; }
  .contacts .accent { color: var(--brand-blue); }

  .address {
    position: absolute;
    right: 70px;
    top: 208px;
    text-align: right;
    font-size: 17px;
    line-height: 25px;
    color: var(--ink);
  }

  .corner-band { position: absolute; left: 0; bottom: 0; width: 700px; height: 70px; }

  .card-back .brand {
    left: 50%; top: 50%;
    transform: translate(-50%, -50%);
    font-size: 64px;
    gap: 22px;
  }
  .card-back .brand-square { width: 48px; height: 48px; }
</style>
</head>
<body>

<section class="card card-front">
  <div class="brand"><span class="brand-square"></span><span class="brand-name">KorvalIT</span></div>

  <div class="person">
    <div class="person-name">MAREN HOLT</div>
    <div class="person-role">Business Development Manager</div>
  </div>

  <div class="divider"></div>

  <ul class="contacts">
    <li><svg viewBox="0 0 12 12"><rect x="3" y="0.5" width="6" height="11" rx="1" fill="none" stroke="#1f86c9" stroke-width="1.2"/></svg>+61 (0)412 555 304</li>
    <li><svg viewBox="0 0 12 12"><path d="M1 5 Q6 0 11 5 L9 6 L8 4 L4 4 L3 6 Z M2 7 H10 V11 H2 Z" fill="#1f86c9"/></svg>+61 (0)7 3555 0148</li>
    <li><svg viewBox="0 0 12 12"><path d="M3 1 L5 3 L4 5 Q5 7 7 8 L9 7 L11 9 L9 11 Q2 10 1 3 Z" fill="#1f86c9"/></svg>+61 (0)7 3555 0100</li>
    <li><svg viewBox="0 0 12 12"><rect x="1" y="4" width="10" height="7" fill="#1f86c9"/><rect x="3" y="1" width="6" height="3" fill="none" stroke="#1f86c9"/></svg>+61 (0)7 3555 0199</li>
    <li><svg viewBox="0 0 12 12"><rect x="0.8" y="2.5" width="10.4" height="7.5" fill="none" stroke="#1f86c9" stroke-width="1.2"/><path d="M1 3 L6 7 L11 3" fill="none" stroke="#1f86c9" stroke-width="1.2"/></svg>mholt@korvalit.com.au</li>
    <li><svg viewBox="0 0 12 12"><circle cx="6" cy="6" r="5.2" fill="none" stroke="#1f86c9" stroke-width="1.2"/><path d="M1 6 H11 M6 1 Q2.5 6 6 11 Q9.5 6 6 1" fill="none" stroke="#1f86c9"/></svg><span>www.<span class="accent">korvalit</span>.com.au</span></li>
  </ul>

  <div class="address">22/9 Carrow Lane,<br>Ashgrove QLD 4060</div>

  <svg class="corner-band" viewBox="0 0 700 70" aria-hidden="true">
    <polygon points="318,0 700,0 700,70 262,70" fill="#1f86c9"/>
  </svg>
</section>

<section class="card card-back">
  <div class="brand"><span class="brand-square"></span><span class="brand-name">RouteKor</span></div>
</section>

</body>
</html>
```